Wine label for premium wine of vinery Mirelovac.

Design Premium wine label.

The brand is called Telvora. Brand can be extended to Ambero Telvora. There
The label should be unique and high class feeling.
This is facebook lonk of the winery
https://www.sociloop.net/402918375510264/

On facebook you can see some examole of labels that are used now. Winery is called Mirelovac, so they used letter "M" as a logo in different ways
Updates

Need extra days to review

Target Market(s)

Premium high class yet modern living traditional but also gadget fun.
I have uploaded few inspirational photos that the owner of the vinery likes. Hope it helps.

Industry/Entity Type

Vinery

Requirements
Must have
• Black, gold, silver color to be dominated. Colors that are NOT acceptable are: green, yellow, blue, purple, pink.

The name of the vinary is Mirelovac and it should be on the front label.
Nice to have
• The size of label should fit the Sorbelo application screenshot frame.
Should not have
• Cheap perception of the label and brand

```html
<!DOCTYPE html>
<html lang="en">
<head>
<meta charset="utf-8">
<title>Telvora Wine Label</title>
<link rel="stylesheet" href="https://fonts.googleapis.com/css2?family=Cormorant+Garamond:wght@400;500&family=Roboto:wght@400;700&display=swap">
<style>
  :root {
    --page: #f7f7f7;
    --label-black: #000000;
    --silver: #a8a8a8;
    --silver-light: #bdbdbd;
    --silver-dim: #8e8e8e;
    --hill-dark: #4a4a4a;
    --hill-light: #b0b0b0;
  }
  * { margin: 0; padding: 0; box-sizing: border-box; }
  html, body {
    width: 1200px;
    height: 1000px;
    overflow: hidden;
    background: var(--page);
  }
  .wine-label {
    position: absolute;
    left: 442px;
    top: 312px;
    width: 308px;
    height: 404px;
    background: var(--label-black);
    overflow: hidden;
  }
  .monogram {
    position: absolute;
    left: 109px;
    top: 28px;
    width: 90px;
    height: 90px;
  }
  .winery-name {
    position: absolute;
    left: 0;
    width: 100%;
    top: 124px;
    text-align: center;
    font-family: "Cormorant Garamond", serif;
    font-weight: 400;
    font-size: 22px;
    letter-spacing: 0.5px;
    color: var(--silver-dim);
  }
  .name-rule {
    position: absolute;
    left: 53px;
    top: 153px;
    width: 202px;
    height: 2px;
    background: var(--silver-dim);
  }
  .wine-name {
    position: absolute;
    left: 0;
    width: 100%;
    top: 166px;
    text-align: center;
    font-family: "Roboto", sans-serif;
    font-weight: 700;
    font-size: 19px;
    letter-spacing: 2px;
    color: var(--silver-light);
  }
  .wine-origin {
    position: absolute;
    left: 0;
    width: 100%;
    top: 195px;
    text-align: center;
    font-family: "Roboto", sans-serif;
    font-weight: 400;
    font-size: 12px;
    letter-spacing: 2px;
    color: var(--silver);
  }
  .vintage {
    position: absolute;
    left: 0;
    width: 100%;
    top: 218px;
    text-align: center;
    font-family: "Roboto", sans-serif;
    font-weight: 700;
    font-size: 12px;
    letter-spacing: 1.5px;
    color: var(--silver-light);
  }
  .vineyard-scene {
    position: absolute;
    left: 0;
    top: 238px;
    width: 308px;
    height: 166px;
    background: linear-gradient(180deg, var(--label-black) 0%, var(--hill-dark) 35%, #3a3a3a 55%, #6e6e6e 100%);
  }
</style>
</head>
<body>
  <main class="wine-label">
    <svg class="monogram" viewBox="0 0 90 90" aria-hidden="true">
      <circle cx="45" cy="45" r="38" fill="none" stroke="#8e8e8e" stroke-width="2"/>
      <text x="45" y="58" text-anchor="middle" font-family="Cormorant Garamond, serif" font-size="38" fill="#8e8e8e">M</text>
    </svg>
    <div class="winery-name">MIRELOVAC</div>
    <div class="name-rule"></div>
    <div class="wine-name">TELVORA</div>
    <div class="wine-origin">CROATIA</div>
    <div class="vintage">2015</div>
    <div class="vineyard-scene" role="img" aria-label="Illustration of rolling vineyard rows in silver lines beneath a dark grey hill"></div>
  </main>
</body>
</html>
```